KRWB new business card design

We need a business card design for our established business which is Australia wide however based in Melbourne. We are a young team of Financial Planners who specialize in Insurance and Basic super advice for people like us.

We are people who help our clients get things done in a timely and cost effective manner whilst having a good time and a laugh along the way.

We would like this to have a consistent feel with our new e-brochure which i have attached from a color and font perspective.

Industry/Entity Type

Business

Requirements
Must have
• We do not need specific address details rather just the states we are in:

VIC/NSW/QLD/TAS
Nice to have
• Curved edge to mate the brochure

```html
<!DOCTYPE html>
<html lang="en">
<head>
<meta charset="utf-8">
<title>KRWB business card</title>
<link rel="stylesheet" href="https://fonts.googleapis.com/css2?family=Arimo:wght@400;700&display=swap">
<style>
  :root {
    --page-bg: #e9e7e2;
    --card-dark: #121613;
    --card-mid: #1d2a1c;
    --lime: #a6d94a;
    --leaf: #5fae4f;
    --text-light: #f2f5ee;
    --text-soft: #d7dccf;
  }
  html, body {
    margin: 0;
    width: 1200px;
    height: 900px;
    overflow: hidden;
    background: var(--page-bg);
    font-family: "Arimo", Arial, sans-serif;
  }
  .canvas {
    position: relative;
    width: 1200px;
    height: 900px;
  }
  .card {
    position: absolute;
    width: 660px;
    height: 378px;
    border-radius: 6px;
    overflow: hidden;
    box-shadow: 0 6px 18px rgba(0,0,0,0.25);
  }
  .card--front { left: 60px; top: 70px; }
  .card--back { left: 480px; top: 470px; }
  .card__texture {
    position: absolute;
    inset: 0;
    background:
      radial-gradient(ellipse at 60% 40%, var(--card-mid) 0%, var(--card-dark) 75%);
  }
  .card__frame {
    position: absolute;
    inset: 0;
  }
  .brand {
    position: absolute;
    display: flex;
    align-items: center;
    gap: 14px;
    color: var(--text-light);
    font-weight: 700;
    line-height: 1;
  }
  .brand__square {
    background: var(--lime);
    flex: none;
  }
  .brand--hero {
    left: 150px;
    top: 150px;
    font-size: 40px;
  }
  .brand--hero .brand__square { width: 70px; height: 70px; }
  .brand--corner {
    right: 150px;
    top: 30px;
    font-size: 18px;
  }
  .brand--back {
    left: 180px;
    top: 100px;
    font-size: 22px;
  }
  .brand--back .brand__square { width: 44px; height: 44px; }
  .contact {
    position: absolute;
    right: 42px;
    top: 128px;
    margin: 0;
    padding: 0;
    list-style: none;
    text-align: right;
    color: var(--text-soft);
    font-size: 16px;
    line-height: 30px;
  }
  .states {
    position: absolute;
    left: 80px;
    bottom: 34px;
    margin: 0;
    padding: 0;
    list-style: none;
    color: var(--text-soft);
    font-size: 15px;
    line-height: 19px;
    letter-spacing: 0.5px;
  }
</style>
</head>
<body>
<main class="canvas">

  <section class="card card--front" aria-label="Card front">
    <div class="card__texture" role="img" aria-label="Dark green geometric lattice background pattern"></div>
    <svg class="card__frame" viewBox="0 0 660 378" aria-hidden="true">
      <path d="M0 78 H560 Q600 78 600 118 V190" fill="none" stroke="var(--lime)" stroke-width="12"/>
      <path d="M150 60 V300 Q150 330 180 330 H660" fill="none" stroke="var(--leaf)" stroke-width="12"/>
    </svg>
    <div class="brand brand--hero">
      <span class="brand__square"></span>
      <span class="brand__name">Kerr Ridge Wealth</span>
    </div>
  </section>

  <section class="card card--back" aria-label="Card back">
    <div class="card__texture" role="img" aria-label="Dark green geometric lattice background pattern"></div>
    <svg class="card__frame" viewBox="0 0 660 378" aria-hidden="true">
      <path d="M0 28 H600 Q632 28 632 60 V150" fill="none" stroke="var(--leaf)" stroke-width="5"/>
      <path d="M30 240 V330 Q30 352 52 352 H660" fill="none" stroke="var(--lime)" stroke-width="5"/>
    </svg>
    <div class="brand brand--back">
      <span class="brand__square"></span>
      <span class="brand__name">Kerr Ridge Wealth</span>
    </div>
    <ul class="contact">
      <li>1300 555 014</li>
      <li>admin@krwb.com.au</li>
      <li>www.kerrridgewealth.com.au</li>
    </ul>
    <ul class="states">
      <li>TASMANIA</li>
      <li>VICTORIA</li>
      <li>GOLD COAST</li>
      <li>NEW SOUTH WALES</li>
    </ul>
  </section>

</main>
</body>
</html>
```